National Sales - Pick Up Truck Dealer

We need a logo design for a new vehicle dealership based in Sydney, Australia. The business name is Coastal Iron Haulers Motor Co. We will be selling American 'trucks/pick up trucks' like KRV, Torvan, Blaxer, Morrow T420, Kenzo Raptors, Morrow T640 and the likes.

These vehicles are a luxury option and we would like the logo to be strong, luxurious and masculine.Colours will be black and red or black and blue with the option of grey and white.

Target Market(s)

Men

Industry/Entity Type

Car Dealer

Contact Information for Business Card

Dennis Harlowe
Managing Director
0412 639 274
den@qelvtrk.com.au

Level 8, Brindle Parkway
17 Pemberly Lane
Carrowby Heights
NSW
Australia
Licence No: MD493152

Back of the card

qelvtrk.com.au

Font styles to use
Sans Serif

Colors

Designer to choose colors to be used in the design.

Requirements
Must have
• The company logo that is in the attachments, you can choose from the three which one you would like to work with. Must have vehicle images ....Please look at the attachments as they show examples of what we like and also provides potential images. If you choose to put an image on the front even if it is just the front of the vehicle can you please use the Black KRV Sorrento. Must have all details from the business card details section front and back
Nice to have
• N/A
Should not have
• No cars or standard trucks, please refer to the attached images to understand the product . Should not have any new logos or branding. No other colours besides what is in the logo you choose.

```html
<!DOCTYPE html>
<html lang="en">
<head>
<meta charset="utf-8">
<title>Coastal Iron Haulers Motor Co – Business Card</title>
<link rel="stylesheet" href="https://fonts.googleapis.com/css2?family=Open+Sans:wght@300;400;600&family=Oswald:wght@600&display=swap">
<style>
  :root {
    --backdrop: #3a3a3b;
    --card: #232324;
    --ink: #ffffff;
    --ink-soft: #d9d9d9;
    --ink-muted: #8a8a8c;
    --accent: #1f78c8;
    --rule: #e6e6e6;
  }
  * { box-sizing: border-box; margin: 0; padding: 0; }
  html, body {
    width: 1200px; height: 900px; overflow: hidden;
    background: var(--backdrop);
    font-family: "Open Sans", Arial, sans-serif;
    color: var(--ink);
  }
  .stage { position: relative; width: 1200px; height: 900px; }
  .card {
    position: absolute;
    width: 660px; height: 400px;
    background: var(--card);
    box-shadow: 0 14px 30px rgba(0,0,0,.45);
  }
  .card--back { left: 340px; top: 30px; }
  .card--front { left: 200px; top: 470px; }

  .wordmark {
    font-family: "Open Sans", Arial, sans-serif;
    font-weight: 600;
    text-transform: uppercase;
    letter-spacing: 2px;
    line-height: 1.15;
    text-align: center;
    white-space: nowrap;
  }
  .card--back .wordmark {
    position: absolute; left: 0; right: 0; top: 130px;
    font-size: 34px; color: var(--ink-muted);
  }
  .web-line { font-weight: 300; letter-spacing: 1.5px; color: var(--ink-soft); }
  .web-line .domain-name { color: var(--accent); }
  .card--back .web-line {
    position: absolute; left: 0; right: 0; bottom: 48px;
    text-align: center; font-size: 16px;
  }

  .card--front .wordmark {
    position: absolute; right: 40px; top: 44px; width: 340px;
    font-size: 22px; color: var(--ink);
  }
  .person { position: absolute; left: 48px; top: 150px; }
  .person__name {
    font-family: "Oswald", "Arial Narrow", sans-serif;
    font-weight: 600; font-size: 40px; line-height: 1;
    text-transform: uppercase; letter-spacing: .5px;
  }
  .person__role { font-weight: 600; font-size: 18px; margin-top: 4px; letter-spacing: .5px; }
  .divider {
    position: absolute; left: 36px; right: 40px; top: 236px;
    height: 1.5px; background: var(--rule);
  }
  .contacts { position: absolute; left: 44px; top: 254px; list-style: none; }
  .contacts li {
    display: flex; align-items: center; gap: 14px;
    font-weight: 300; font-size: 18px; line-height: 30px; letter-spacing: .5px;
  }
  .contacts svg { width: 18px; height: 18px; flex: none; }
  .licence {
    position: absolute; right: 40px; top: 200px;
    font-size: 18px; font-weight: 400;
  }
  .licence__label { color: var(--accent); }
  .address {
    position: absolute; right: 40px; bottom: 40px;
    text-align: right; font-weight: 400; font-size: 18px; line-height: 27px;
    font-style: normal;
    color: var(--ink-soft);
  }
</style>
</head>
<body>
<main class="stage">
  <section class="card card--back" aria-label="Card back">
    <div class="wordmark">Coastal Iron Haulers<br>Motor Co</div>
    <p class="web-line">www.<span class="domain-name">qelvtrk</span>.com.au</p>
  </section>

  <section class="card card--front" aria-label="Card front">
    <div class="wordmark">Coastal Iron Haulers<br>Motor Co</div>

    <div class="person">
      <h1 class="person__name">Dennis Harlowe</h1>
      <p class="person__role">Managing Director</p>
    </div>

    <p class="licence"><span class="licence__label">Licence No:</span> MD493152</p>

    <div class="divider"></div>

    <ul class="contacts">
      <li>
        <svg viewBox="0 0 18 18" aria-hidden="true"><rect x="5" y="1.5" width="8" height="15" rx="1.5" fill="none" stroke="var(--accent)" stroke-width="1.6"/><line x1="8" y1="14" x2="10" y2="14" stroke="var(--accent)" stroke-width="1.6"/></svg>
        0412 639 274
      </li>
      <li>
        <svg viewBox="0 0 18 18" aria-hidden="true"><rect x="1.5" y="4" width="15" height="10" fill="none" stroke="var(--accent)" stroke-width="1.6"/><polyline points="1.5,4 9,10 16.5,4" fill="none" stroke="var(--accent)" stroke-width="1.6"/></svg>
        den@qelvtrk.com.au
      </li>
      <li>
        <svg viewBox="0 0 18 18" aria-hidden="true"><circle cx="9" cy="9" r="7.5" fill="none" stroke="var(--accent)" stroke-width="1.6"/><ellipse cx="9" cy="9" rx="3.2" ry="7.5" fill="none" stroke="var(--accent)" stroke-width="1.2"/><line x1="1.5" y1="9" x2="16.5" y2="9" stroke="var(--accent)" stroke-width="1.2"/></svg>
        <span class="web-line">www.<span class="domain-name">qelvtrk</span>.com.au</span>
      </li>
    </ul>

    <address class="address">
      Level 8, Brindle Parkway,<br>
      17 Pemberly Lane, Carrowby Heights,<br>
      NSW, Australia
    </address>
  </section>
</main>
</body>
</html>
```